Copperleaf Roofing Business Card

This is my current business card. But I’d like to make some changes. Somewhere on the card I’d like to list some of the services we offer. Maybe on the back? But I’d still like to keep the red. White and black modern look.

-residential & commercial roofing
-Roof Repairs & Maintenance
-Storm Damage & Insurance Claims specialist
-Christmas Lights and permanent Christmas lights
Fencing. Windows. Gutters. Siding. Sheetrock, painting.

```html
<!DOCTYPE html>
<html lang="en">
<head>
<meta charset="utf-8">
<title>Copperleaf Roofing Co. – Business Card</title>
<link rel="stylesheet" href="https://fonts.googleapis.com/css2?family=Audiowide&family=Poppins:wght@400;700&display=swap">
<style>
  :root {
    --bg: #9a9a9a;
    --red: #e30613;
    --red-dark: #8b0a14;
    --ink: #111111;
    --black: #000000;
    --white: #ffffff;
    --card-w: 580px;
    --card-h: 358px;
  }
  * { box-sizing: border-box; margin: 0; padding: 0; }
  html, body { width: 1093px; height: 1200px; overflow: hidden; }
  body {
    background: var(--bg);
    font-family: "Poppins", sans-serif;
    position: relative;
  }
  .card {
    position: absolute;
    left: 264px;
    width: var(--card-w);
    height: var(--card-h);
    overflow: hidden;
  }
  .card--front { top: 226px; background: var(--white); color: var(--ink); }
  .card--back { top: 620px; background: var(--black); color: var(--white); }

  .name-block { position: absolute; left: 26px; top: 42px; }
  .name-block__accent {
    position: absolute; left: -26px; top: 3px;
    width: 13px; height: 31px; background: var(--red);
  }
  .name-block__name {
    font-family: "Audiowide", sans-serif;
    font-size: 17px; letter-spacing: 0.5px;
    color: var(--red); line-height: 1.2;
  }
  .name-block__title { font-size: 15px; line-height: 1.3; margin-top: 1px; }
  .name-block__rule {
    width: 32px; height: 1px; background: var(--red); margin-top: 8px;
  }

  .contact-list { position: absolute; left: 22px; top: 238px; list-style: none; }
  .contact-list__item {
    display: flex; align-items: center; gap: 3px;
    height: 26.5px; font-size: 16.5px;
  }
  .contact-list__icon { width: 24px; height: 24px; flex: none; }

  .brand { position: absolute; text-align: center; }
  .brand__mark {
    display: block; margin: 0 auto;
    border-radius: 50%; background: var(--red);
  }
  .brand__name {
    font-weight: 700; color: var(--red);
    line-height: 1.05; letter-spacing: 1px; text-transform: uppercase;
  }
  .card--front .brand { left: 302px; top: 58px; width: 240px; }
  .card--front .brand__mark { width: 132px; height: 132px; }
  .card--front .brand__name { font-size: 27px; margin-top: 22px; }
  .card--back .brand { left: 322px; top: 32px; width: 240px; }
  .card--back .brand__mark { width: 118px; height: 118px; border: 2px solid var(--white); }
  .card--back .brand__name { font-size: 24px; margin-top: 18px; }

  .service-list { position: absolute; left: 30px; list-style: none; }
  .service-list--trades { top: 33px; }
  .service-list--roofing { top: 240px; }
  .service-list__item {
    display: flex; align-items: center; gap: 5px;
    height: 21.8px; font-size: 15.5px; letter-spacing: 0.2px;
  }
  .service-list__icon { width: 15px; height: 15px; flex: none; }

  .card__band {
    position: absolute; left: 0; bottom: 0; width: 100%; height: 13px;
    background: linear-gradient(90deg, var(--red-dark) 0%, var(--red-dark) 49%, var(--red) 50%, var(--red) 100%);
  }
</style>
</head>
<body>

<section class="card card--front" aria-label="Business card front">
  <div class="name-block">
    <span class="name-block__accent"></span>
    <h1 class="name-block__name">DALE MERCER</h1>
    <p class="name-block__title">OWNER</p>
    <div class="name-block__rule"></div>
  </div>

  <ul class="contact-list">
    <li class="contact-list__item">
      <svg class="contact-list__icon" viewBox="0 0 24 24" aria-hidden="true">
        <circle cx="12" cy="12" r="12" fill="#e30613"/>
        <path d="M8.5 6.5l2 2.4-1.2 1.4c.8 1.7 2 2.9 3.6 3.7l1.4-1.2 2.4 2-1.3 1.8c-4-.6-7.4-4-8-8z" fill="none" stroke="#fff" stroke-width="1.3" stroke-linejoin="round"/>
      </svg>
      682-555-0148
    </li>
    <li class="contact-list__item">
      <svg class="contact-list__icon" viewBox="0 0 24 24" aria-hidden="true">
        <circle cx="12" cy="12" r="12" fill="#e30613"/>
        <rect x="6" y="8" width="12" height="8.5" fill="none" stroke="#fff" stroke-width="1.2"/>
        <path d="M6 8l6 5 6-5M6 16.5l4.3-4M18 16.5l-4.3-4" fill="none" stroke="#fff" stroke-width="1.2"/>
      </svg>
      dale@copperleafroofing.co
    </li>
    <li class="contact-list__item">
      <svg class="contact-list__icon" viewBox="0 0 24 24" aria-hidden="true">
        <circle cx="12" cy="12" r="12" fill="#e30613"/>
        <g fill="none" stroke="#fff" stroke-width="1.1">
          <circle cx="12" cy="12" r="6"/>
          <ellipse cx="12" cy="12" rx="2.6" ry="6"/>
          <path d="M6 12h12M7 9h10M7 15h10"/>
        </g>
      </svg>
      www.copperleafroofing.co
    </li>
  </ul>

  <div class="brand">
    <span class="brand__mark" aria-hidden="true"></span>
    <p class="brand__name">Copperleaf<br>Roofing Co.</p>
  </div>

  <div class="card__band" role="img" aria-label="Red and dark red plaid band"></div>
</section>

<section class="card card--back" aria-label="Business card back">
  <ul class="service-list service-list--trades">
    <li class="service-list__item"><svg class="service-list__icon" viewBox="0 0 16 16" aria-hidden="true"><path d="M8 1l7 7-7 7-7-7z" fill="none" stroke="#e30613" stroke-width="1.3"/><path d="M8 4.5L11.5 8 8 11.5 4.5 8z" fill="#e30613"/></svg>Fencing</li>
    <li class="service-list__item"><svg class="service-list__icon" viewBox="0 0 16 16" aria-hidden="true"><path d="M8 1l7 7-7 7-7-7z" fill="none" stroke="#e30613" stroke-width="1.3"/><path d="M8 4.5L11.5 8 8 11.5 4.5 8z" fill="#e30613"/></svg>Windows</li>
    <li class="service-list__item"><svg class="service-list__icon" viewBox="0 0 16 16" aria-hidden="true"><path d="M8 1l7 7-7 7-7-7z" fill="none" stroke="#e30613" stroke-width="1.3"/><path d="M8 4.5L11.5 8 8 11.5 4.5 8z" fill="#e30613"/></svg>Gutters</li>
    <li class="service-list__item"><svg class="service-list__icon" viewBox="0 0 16 16" aria-hidden="true"><path d="M8 1l7 7-7 7-7-7z" fill="none" stroke="#e30613" stroke-width="1.3"/><path d="M8 4.5L11.5 8 8 11.5 4.5 8z" fill="#e30613"/></svg>Siding</li>
    <li class="service-list__item"><svg class="service-list__icon" viewBox="0 0 16 16" aria-hidden="true"><path d="M8 1l7 7-7 7-7-7z" fill="none" stroke="#e30613" stroke-width="1.3"/><path d="M8 4.5L11.5 8 8 11.5 4.5 8z" fill="#e30613"/></svg>Sheetrock</li>
    <li class="service-list__item"><svg class="service-list__icon" viewBox="0 0 16 16" aria-hidden="true"><path d="M8 1l7 7-7 7-7-7z" fill="none" stroke="#e30613" stroke-width="1.3"/><path d="M8 4.5L11.5 8 8 11.5 4.5 8z" fill="#e30613"/></svg>Painting.</li>
  </ul>

  <div class="brand">
    <span class="brand__mark" aria-hidden="true"></span>
    <p class="brand__name">Copperleaf<br>Roofing Co.</p>
  </div>

  <ul class="service-list service-list--roofing">
    <li class="service-list__item"><svg class="service-list__icon" viewBox="0 0 16 16" aria-hidden="true"><path d="M8 1l7 7-7 7-7-7z" fill="none" stroke="#e30613" stroke-width="1.3"/><path d="M8 4.5L11.5 8 8 11.5 4.5 8z" fill="#e30613"/></svg>Residential &amp; Commercial Roofing</li>
    <li class="service-list__item"><svg class="service-list__icon" viewBox="0 0 16 16" aria-hidden="true"><path d="M8 1l7 7-7 7-7-7z" fill="none" stroke="#e30613" stroke-width="1.3"/><path d="M8 4.5L11.5 8 8 11.5 4.5 8z" fill="#e30613"/></svg>Roof Repairs &amp; Maintenance</li>
    <li class="service-list__item"><svg class="service-list__icon" viewBox="0 0 16 16" aria-hidden="true"><path d="M8 1l7 7-7 7-7-7z" fill="none" stroke="#e30613" stroke-width="1.3"/><path d="M8 4.5L11.5 8 8 11.5 4.5 8z" fill="#e30613"/></svg>Storm Damage &amp; Insurance Claims Specialist</li>
    <li class="service-list__item"><svg class="service-list__icon" viewBox="0 0 16 16" aria-hidden="true"><path d="M8 1l7 7-7 7-7-7z" fill="none" stroke="#e30613" stroke-width="1.3"/><path d="M8 4.5L11.5 8 8 11.5 4.5 8z" fill="#e30613"/></svg>Christmas Lights and Permanent Christmas Lights</li>
  </ul>

  <div class="card__band" role="img" aria-label="Red and dark red plaid band"></div>
</section>

</body>
</html>
```